Fresh new and cool frozen burger box! Come be a part of an amazing project!

Crust Drums and Melts restaurant is expanding into the frozen foods market!
please check out our website to understand the vibe of the company
https://crumbvale.ca
this is a line of premium Halal meat, we want to stress our top-notch quality.
we like the orange colours so see what you can do with them. (maybe white and orange combo)
you have lots of creative freedom here, feel free to use the burger photo I am attaching or any image off the website.
logo should be nice and visible.
we want this packaging to really stand out and be special.
Come be a part of an amazing project!
Muslim Flails, looking of a quality meat burger. mostly already familiar with our brand
Frozen food

```html
<!DOCTYPE html>
<html lang="en">
<head>
<meta charset="utf-8">
<title>Crumbvale Burger Box</title>
<link rel="stylesheet" href="https://fonts.googleapis.com/css2?family=Anton&family=Archivo+Black&family=Roboto:wght@400;700&display=swap">
<style>
  :root {
    --stage: #d4d4d4;
    --lid-white: #f7f7f5;
    --orange: #e9a213;
    --orange-deep: #d48f0a;
    --base-red: #8e1b2c;
    --ink: #141414;
    --white: #ffffff;
    --chili: #d6281c;
    --photo-warm: #c98a45;
    --photo-warm-soft: #d9a465;
  }
  * { box-sizing: border-box; margin: 0; padding: 0; }
  html, body { width: 1200px; height: 724px; overflow: hidden; }
  body {
    background: var(--stage);
    font-family: "Roboto", sans-serif;
    position: relative;
  }
  .box-art { position: absolute; left: 150px; top: 40px; width: 900px; height: 644px; }

  .lid {
    position: absolute; left: 0; top: 0; width: 620px; height: 340px;
    background: var(--lid-white);
  }
  .lid__photo {
    position: absolute; left: 60px; top: 50px; width: 380px; height: 230px;
    border-radius: 12px;
    background: linear-gradient(180deg, var(--photo-warm-soft), var(--photo-warm));
  }
  .lid__brand {
    position: absolute; right: 28px; top: 48px; text-align: right;
  }
  .lid__brand .brand-name { font-size: 26px; color: var(--ink); }
  .lid__brand .tagline { font-size: 10px; margin-top: 4px; word-spacing: 2px; }

  .front {
    position: absolute; left: 0; top: 340px; width: 620px; height: 190px;
    background: var(--orange);
    display: flex; flex-direction: column; justify-content: center; padding-left: 70px;
  }
  .brand { display: flex; align-items: center; gap: 14px; }
  .brand-mark {
    width: 56px; height: 56px; border-radius: 50%; background: var(--white);
    flex: none;
  }
  .brand-name {
    font-family: "Anton", sans-serif; font-size: 64px; line-height: 1;
    color: var(--white); letter-spacing: 1px;
  }
  .tagline {
    font-family: "Archivo Black", sans-serif; font-size: 24px; color: var(--ink);
    margin-top: 8px; word-spacing: 4px;
  }
  .tagline .dot { color: var(--chili); }

  .side {
    position: absolute; left: 620px; top: 340px; width: 280px; height: 190px;
    background: var(--orange-deep);
    display: flex; gap: 14px; padding: 18px 16px;
  }
  .side__photo {
    width: 104px; height: 120px; flex: none; margin-top: 24px;
    border-radius: 10px;
    background: linear-gradient(180deg, var(--photo-warm-soft), var(--photo-warm));
  }
  .side__copy { display: flex; flex-direction: column; gap: 4px; min-width: 0; }
  .side__copy .brand { gap: 6px; }
  .side__copy .brand-mark { width: 18px; height: 18px; }
  .side__copy .brand-name { font-size: 22px; }
  .side__copy .tagline { font-size: 9px; margin-top: 0; word-spacing: 1px; }
  .side__text { font-size: 8.5px; line-height: 1.35; color: var(--ink); margin-top: 4px; }

  .base {
    position: absolute; left: 0; top: 530px; width: 900px; height: 114px;
    background: var(--base-red);
  }
</style>
</head>
<body>
  <main class="box-art">
    <section class="lid">
      <div class="lid__photo" role="img" aria-label="Photo of a sesame bun burger with beef patty, bacon, cheese, tomato and lettuce"></div>
      <div class="lid__brand">
        <div class="brand-name">CRUMBVALE</div>
        <div class="tagline">Crust <span class="dot">•</span> Drums <span class="dot">•</span> Melts</div>
      </div>
    </section>

    <section class="front">
      <div class="brand">
        <span class="brand-mark"></span>
        <span class="brand-name">CRUMBVALE</span>
      </div>
      <div class="tagline">Crust <span class="dot">•</span> Drums <span class="dot">•</span> Melts</div>
    </section>

    <section class="side">
      <div class="side__photo" role="img" aria-label="Photo of a stacked burger with bacon, cheese and lettuce"></div>
      <div class="side__copy">
        <div class="brand">
          <span class="brand-mark"></span>
          <span class="brand-name">CRUMBVALE</span>
        </div>
        <div class="tagline">Crust <span class="dot">•</span> Drums <span class="dot">•</span> Melts</div>
        <p class="side__text">Premium halal beef, pressed fresh and frozen fast to lock in flavour. Grill straight from frozen for a juicy, tender patty every time. Quality you can taste in every single bite, made with care for your family table.</p>
      </div>
    </section>

    <section class="base" role="img" aria-label="Deep red base with a light geometric line pattern"></section>
  </main>
</body>
</html>
```